"Vine Hollow Excursions" is a top notch Santa Barbara County Wine Tour company.

We provide scenic, boutique and custom wine tours. I need the card to be clean and classy. I will provide our logo. I would like the logo to cover the back side of the card as an option and would like to see a couple color options other then our signature green and gold. I would like to see some creative options and let the designers come up with options.
I need cards for myself and my team. The final design should communicate "An authentic and boutique wine tour experience"
Please use my website for reference www.vinehollowexcursions.example

Target Market(s)

We have a wide range of clients from millennials to baby boomers

Industry/Entity Type

Tour

Contact Information for Business Card

Contact info:
Dale Morton
805-219-6384
info@vinehollowexcursions.example
vinehollowexcursions.example

Colors

Designer to choose colors to be used in the design.

Requirements
Must have
• my logo
Nice to have
• *I would like to have the backside side with the logo and the company statement
• "An authentic and boutique wine tour experience" as an option.
• *I would also like to see what the designers can create!
• *I would like to see an option that incorporates or social: instagram, yelp, trip advisor
Should not have
• I do not want it too busy.

```html
<!DOCTYPE html>
<html lang="en">
<head>
<meta charset="utf-8">
<title>Vine Hollow Excursions – Business Card</title>
<link rel="stylesheet" href="https://fonts.googleapis.com/css2?family=Roboto:wght@400;500&family=Roboto+Condensed:wght@700&display=swap">
<style>
  :root {
    --backdrop: #2b2b2b;
    --card-paper: #f1f2f1;
    --scene-tint: #dde4df;
    --scene-tint-soft: #e8ece9;
    --brand-green: #256843;
    --ink-grey: #545454;
    --on-green: #ffffff;
    --chip-tan: #c9b48f;
    --chip-green: #5f9a3c;
    --chip-red: #d8282a;
  }
  * { margin: 0; padding: 0; box-sizing: border-box; }
  html, body {
    width: 1200px;
    height: 960px;
    overflow: hidden;
    background: var(--backdrop);
  }
  .stage {
    position: relative;
    width: 1200px;
    height: 960px;
  }
  .card {
    position: absolute;
    width: 600px;
    height: 343px;
    box-shadow: 0 2px 6px rgba(0, 0, 0, 0.45);
    overflow: hidden;
  }
  .card--front {
    left: 314px;
    top: 113px;
    background: var(--card-paper);
  }
  .card--back {
    left: 311px;
    top: 472px;
    background: var(--brand-green);
  }

  /* Front */
  .landscape-backdrop {
    position: absolute;
    left: 0;
    right: 0;
    bottom: 0;
    height: 290px;
    background:
      radial-gradient(ellipse 240px 170px at 130px 230px, var(--scene-tint-soft) 0%, rgba(232, 236, 233, 0) 100%),
      linear-gradient(to bottom, rgba(221, 228, 223, 0) 0%, rgba(221, 228, 223, 0.55) 55%, var(--scene-tint) 100%);
  }
  .brand-mark {
    position: absolute;
    right: 40px;
    top: 42px;
    width: 240px;
    display: flex;
    flex-direction: column;
    align-items: center;
  }
  .brand-mark__dot {
    width: 58px;
    height: 58px;
    border-radius: 50%;
    background: var(--brand-green);
    margin-bottom: 16px;
  }
  .brand-name {
    font-family: "Roboto", sans-serif;
    font-weight: 500;
    text-transform: uppercase;
    text-align: center;
  }
  .card--front .brand-name {
    font-size: 22px;
    line-height: 27px;
    letter-spacing: 1.5px;
    color: var(--brand-green);
  }
  .contact-list {
    position: absolute;
    left: 42px;
    top: 246px;
    list-style: none;
    font-family: "Roboto", sans-serif;
    font-size: 14.5px;
    color: var(--ink-grey);
  }
  .contact-list li {
    display: flex;
    align-items: center;
    height: 19.5px;
  }
  .contact-list svg {
    width: 13px;
    height: 13px;
    margin-right: 8px;
    fill: var(--brand-green);
    flex: none;
  }
  .person-name {
    position: absolute;
    right: 40px;
    top: 281px;
    font-family: "Roboto Condensed", sans-serif;
    font-weight: 700;
    font-size: 21px;
    text-transform: uppercase;
    color: var(--brand-green);
  }

  /* Back */
  .social-links {
    position: absolute;
    right: 30px;
    top: 29px;
    display: flex;
    gap: 4px;
  }
  .social-links span {
    width: 31px;
    height: 31px;
    border-radius: 5px;
    box-shadow: 0 1px 2px rgba(0, 0, 0, 0.35);
  }
  .social-links .chip--tan { background: var(--chip-tan); }
  .social-links .chip--green { background: var(--chip-green); }
  .social-links .chip--red { background: var(--chip-red); }
  .card--back .brand-name {
    position: absolute;
    left: 0;
    right: 0;
    top: 122px;
    font-size: 40px;
    line-height: 48px;
    letter-spacing: 2px;
    color: var(--on-green);
  }
  .statement {
    position: absolute;
    left: 0;
    right: 0;
    top: 292px;
    text-align: center;
    font-family: "Roboto", sans-serif;
    font-size: 15.2px;
    color: var(--on-green);
  }
</style>
</head>
<body>
<main class="stage">
  <section class="card card--front" aria-label="Card front">
    <div class="landscape-backdrop" role="img" aria-label="Faint backdrop of sunrise over hills and vineyard rows"></div>
    <div class="brand-mark">
      <span class="brand-mark__dot" aria-hidden="true"></span>
      <p class="brand-name">Vine Hollow<br>Excursions</p>
    </div>
    <ul class="contact-list">
      <li>
        <svg viewBox="0 0 16 16" aria-hidden="true"><path d="M3.6 1.2l2.4 2.8-1.3 2c.9 2 2.4 3.5 4.4 4.4l2-1.3 2.8 2.4-1.4 2.6C7 13.6 2.4 9 1 3z"/></svg>
        805-219-6384
      </li>
      <li>
        <svg viewBox="0 0 16 16" aria-hidden="true"><path d="M1 3h14v1.5L8 9 1 4.5z M1 6.2l7 4.5 7-4.5V13H1z"/></svg>
        info@vinehollowexcursions.example
      </li>
      <li>
        <svg viewBox="0 0 16 16" aria-hidden="true"><path d="M8 1a7 7 0 1 0 0 14A7 7 0 0 0 8 1zm-1 2.5c1 .6 1.8 1.6 1.4 2.6-.5 1-2 .6-2.4 1.7-.3 1 .9 1.6.6 2.8-.2.8-1 1.3-1.6 1.9A5 5 0 0 1 7 3.5zm3.5 8.8c-.5-.9 0-2 .9-2.5.8-.4 1.6-.1 1.9.3a5 5 0 0 1-2.8 2.2z"/></svg>
        vinehollowexcursions.example
      </li>
    </ul>
    <p class="person-name">Dale Morton</p>
  </section>

  <section class="card card--back" aria-label="Card back">
    <div class="social-links" aria-label="Social profiles">
      <span class="chip--tan"></span><span class="chip--green"></span><span class="chip--red"></span>
    </div>
    <p class="brand-name">Vine Hollow<br>Excursions</p>
    <p class="statement">An authentic &amp; boutique wine tour experience</p>
  </section>
</main>
</body>
</html>
```